Business Card front and back

I am looking for business card design. I really really like the design file I uploaded named 627788_19250069_3478263_85f427ee_image

Target Market(s)

Corporate Fitness High end Private country club

Industry/Entity Type

Fitness Industry

Contact Information for Business Card

The last image I like as an example I uploaded a bunch of my logos. The file labeled "the signature" is my business card information for you to use

Colors
0054AA
0677BA
7BADD7
CADEEF
E8F1F8

Requirements
Must have
• E-mail sigThe file I uploaded labeled "627788_19250069_3478263_85f427ee_image" with all the plus signs on the back if those could be the logo symbol I uploaded labeled "1 back.png"

```html
<!DOCTYPE html>
<html lang="en">
<head>
<meta charset="utf-8">
<title>Peakform Studio – Business Card Front and Back</title>
<link rel="stylesheet" href="https://fonts.googleapis.com/css2?family=Poppins:wght@300;400;500;600;700&display=swap">
<style>
  :root {
    --backdrop: #262626;
    --card-white: #ffffff;
    --brand-blue: #4a7fc3;
    --brand-blue-deep: #3a6aab;
    --brand-blue-light: #7badd7;
    --ink-dark: #2b2b2b;
    --ink-mid: #3a3a3a;
    --rule-grey: #9a9a9a;
    --photo-dark: #2c2c2c;
    --photo-mid: #4a4a4a;
  }
  * { box-sizing: border-box; margin: 0; padding: 0; }
  html, body {
    width: 1200px;
    height: 1108px;
    overflow: hidden;
    background: var(--backdrop);
    font-family: "Poppins", sans-serif;
  }
  .canvas {
    width: 1200px;
    height: 1108px;
    display: flex;
    align-items: center;
    justify-content: center;
    gap: 80px;
  }
  .card {
    width: 420px;
    height: 720px;
    border-radius: 24px;
    position: relative;
    overflow: hidden;
  }

  /* Front */
  .card-front {
    background: var(--card-white);
    display: flex;
    flex-direction: column;
    align-items: center;
    padding-top: 92px;
  }
  .brand-lockup {
    display: flex;
    align-items: center;
    gap: 12px;
  }
  .brand-square {
    width: 26px;
    height: 26px;
    background: var(--brand-blue);
    border-radius: 4px;
  }
  .brand-name {
    font-weight: 700;
    font-size: 30px;
    letter-spacing: 1px;
    color: var(--ink-dark);
    text-transform: uppercase;
  }
  .portrait {
    margin-top: 58px;
    width: 196px;
    height: 196px;
    border-radius: 50%;
    border: 4px solid var(--brand-blue);
    background: radial-gradient(circle at 50% 45%, var(--photo-mid), var(--photo-dark) 70%);
  }
  .person-name {
    margin-top: 26px;
    font-weight: 700;
    font-size: 36px;
    letter-spacing: -0.5px;
    color: var(--ink-dark);
    text-transform: uppercase;
    line-height: 1;
  }
  .person-name .surname { color: var(--brand-blue); }
  .person-title {
    margin-top: 8px;
    font-weight: 400;
    font-size: 18px;
    letter-spacing: 1px;
    color: var(--ink-mid);
    text-transform: uppercase;
  }
  .contact-icons {
    margin-top: 16px;
    width: 320px;
    display: flex;
    align-items: center;
    gap: 8px;
  }
  .contact-icons .rule {
    flex: 1;
    height: 1px;
    background: var(--rule-grey);
  }
  .icon-tile {
    width: 32px;
    height: 32px;
    background: var(--brand-blue);
    border-radius: 5px;
    display: flex;
    align-items: center;
    justify-content: center;
  }
  .icon-tile svg { width: 20px; height: 20px; }
  .contact-list {
    margin-top: 12px;
    text-align: center;
    font-size: 19px;
    line-height: 1.35;
    color: var(--ink-dark);
    font-weight: 400;
    font-style: normal;
  }
  .contact-rule {
    margin-top: 12px;
    width: 320px;
    height: 1px;
    background: var(--rule-grey);
  }
  .service-area {
    margin-top: 12px;
    font-size: 16px;
    color: var(--ink-dark);
    letter-spacing: 0.5px;
  }

  /* Back */
  .card-back {
    background: var(--brand-blue);
    display: flex;
    align-items: center;
    justify-content: center;
  }
  .pattern-field {
    position: absolute;
    inset: 0;
    background: linear-gradient(160deg, var(--brand-blue) 0%, var(--brand-blue-deep) 50%, var(--brand-blue) 100%);
  }
  .back-brand-name {
    position: relative;
    font-weight: 700;
    font-size: 30px;
    letter-spacing: 1px;
    color: var(--card-white);
    text-transform: uppercase;
  }
</style>
</head>
<body>
<main class="canvas">
  <section class="card card-front" aria-label="Business card front">
    <div class="brand-lockup">
      <span class="brand-square"></span>
      <span class="brand-name">Peakform Studio</span>
    </div>

    <div class="portrait" role="img" aria-label="Portrait photograph of the consultant"></div>

    <h1 class="person-name">Dalen <span class="surname">Morrow</span></h1>
    <p class="person-title">Consultant</p>

    <div class="contact-icons">
      <span class="rule"></span>
      <span class="icon-tile" aria-label="Phone">
        <svg viewBox="0 0 24 24" fill="none" stroke="#fff" stroke-width="2" stroke-linecap="round" stroke-linejoin="round">
          <path d="M5 4h4l2 5-2.5 1.5a11 11 0 0 0 5 5L15 13l5 2v4a2 2 0 0 1-2 2A16 16 0 0 1 3 6a2 2 0 0 1 2-2"/>
        </svg>
      </span>
      <span class="icon-tile" aria-label="Email">
        <svg viewBox="0 0 24 24" fill="none" stroke="#fff" stroke-width="2" stroke-linejoin="round">
          <rect x="3" y="5" width="18" height="14" rx="1"/>
          <path d="M3 6l9 7 9-7"/>
        </svg>
      </span>
      <span class="icon-tile" aria-label="Website">
        <svg viewBox="0 0 24 24" fill="none" stroke="#fff" stroke-width="2">
          <circle cx="12" cy="12" r="9"/>
          <path d="M3 12h18M12 3c3 3 3 15 0 18M12 3c-3 3-3 15 0 18"/>
        </svg>
      </span>
      <span class="rule"></span>
    </div>

    <address class="contact-list">
      555-014-2278<br>
      Dalen@peakformstudio.co<br>
      www.peakformstudio.co
    </address>
    <div class="contact-rule"></div>
    <p class="service-area">NE.NW.SE.SW.CT</p>
  </section>

  <section class="card card-back" aria-label="Business card back">
    <div class="pattern-field" role="img" aria-label="Repeating brand name pattern in tone-on-tone blue"></div>
    <p class="back-brand-name">Peakform Studio</p>
  </section>
</main>
</body>
</html>
```